Change of trading name, rebrand

existing website to be updated with new theme and logo. existing website is
www.harlowbrentmere.com.au
Industry/Entity Type
Construction
Coding
Coded - Design and coding required
Number of Pages Required
5+ page
Requirements
Must have
- be mobile phone friendly

```html
<!DOCTYPE html>
<html lang="en">
<head>
<meta charset="utf-8">
<meta name="viewport" content="width=1200">
<title>HBR Plant Hire – Heavy Equipment Hire</title>
<link href="https://fonts.googleapis.com/css2?family=Poppins:wght@400;500;600;700&display=swap" rel="stylesheet">
<style>
:root{
  --navy:#222b6e;
  --navy-dark:#1b2259;
  --blue:#2d4c9f;
  --blue-light:#3c62b8;
  --ink:#222222;
  --text:#444444;
  --grey-band:#f2f2f3;
  --grey-btn:#7d7d7d;
  --white:#ffffff;
  --line:#d9d9d9;
}
*{box-sizing:border-box;margin:0;padding:0}
html,body{width:1200px;height:5263px;overflow:hidden}
body{font-family:"Poppins",sans-serif;color:var(--text);background:var(--white);position:relative}
section,header,footer{position:relative;width:1200px}
.abs{position:absolute}

.btn{position:absolute;display:flex;align-items:center;justify-content:center;gap:10px;border-radius:40px;font-weight:500;text-transform:uppercase;white-space:nowrap}
.btn .arr{width:18px;height:18px;border-radius:50%;display:inline-flex;align-items:center;justify-content:center}
.btn-navy{background:var(--navy);color:var(--white);font-size:12px}
.btn-navy .arr{background:var(--white)}
.btn-white{background:var(--white);color:var(--navy);font-size:15px}
.btn-white .arr{background:var(--navy)}
.btn-grey{background:var(--grey-btn);color:var(--white);font-size:16px}
.btn-grey .arr{background:var(--white);width:24px;height:24px}

.eyebrow{position:absolute;display:flex;align-items:center;gap:10px;font-size:20px;font-weight:400}
.eyebrow .rule{display:flex;align-items:center}
.eyebrow .rule i{display:block;width:6px;height:6px;border-radius:50%;background:currentColor}
.eyebrow .rule b{display:block;height:2px;width:110px;background:currentColor}

.site-header{height:141px;background:var(--white)}
.brand{left:76px;top:14px;width:170px;text-align:center;color:var(--navy)}
.brand .mark{font-size:46px;font-weight:700;line-height:52px;letter-spacing:2px}
.brand .sub{font-size:12px;font-weight:600;letter-spacing:4px;color:var(--ink)}
.phone-pill{left:818px;top:33px;width:155px;height:32px;border:2px solid var(--navy);border-radius:20px;background:var(--navy);color:var(--white);font-size:13px;display:flex;align-items:center;gap:12px;padding-left:4px}
.phone-pill .ic{width:26px;height:26px;border-radius:50%;background:var(--white);display:flex;align-items:center;justify-content:center}
.contact-btn{left:985px;top:33px;width:141px;height:32px;border-radius:20px;background:#111;color:var(--white);font-size:12px;font-weight:500;display:flex;align-items:center;justify-content:center}
.main-nav{left:454px;top:84px;font-size:13.5px;color:#444}
.main-nav span{position:absolute;white-space:nowrap;top:0}
.main-nav .active{color:var(--navy);font-weight:500}
.main-nav .active::after{content:"";position:absolute;left:0;right:0;top:26px;height:3px;background:var(--navy)}

.hero{height:564px;background:linear-gradient(90deg,#2a4a9d 0%,#34569f 38%,#7c89a0 60%,#b9a96a 74%,#a9a084 88%,#8f8f8a 100%)}
.hero h1{left:78px;top:122px;font-size:52px;font-weight:600;line-height:62px;color:var(--white)}
.hero p{left:78px;top:272px;font-size:23px;line-height:39px;color:var(--white)}
.hero .btn{left:80px;top:376px;width:188px;height:58px}
.dots{left:552px;top:500px;display:flex;gap:12px;align-items:center}
.dots i{display:block;width:10px;height:10px;border-radius:50%;background:var(--white)}
.dots i.on{width:30px;height:6px;border-radius:3px}

.about{height:582px}
.about .eyebrow{left:129px;top:103px;color:var(--ink)}
.about h2{left:129px;top:136px;font-size:48px;font-weight:500;color:var(--navy)}
.about .copy{left:129px;top:229px;width:516px;font-size:14.5px;line-height:30px;text-align:justify;color:#555}
.about .btn{left:131px;top:443px;width:155px;height:41px}
.photo-frame{left:699px;top:118px;width:380px;height:362px;background:var(--white);border-radius:14px 14px 60px 14px;box-shadow:0 4px 18px rgba(0,0,0,.18);padding:10px}
.photo-frame .ph{width:100%;height:100%;border-radius:8px 8px 52px 8px;background:linear-gradient(135deg,#dfe3e8 0%,#c7ccd3 35%,#4b6aa6 55%,#3c578f 75%,#c46a3a 100%)}

.features{height:337px;background:var(--grey-band)}
.feature{position:absolute;top:64px;width:200px;text-align:center;transform:translateX(-50%)}
.feature .circle{width:135px;height:135px;margin:0 auto;border-radius:50%;border:3px solid var(--navy);display:flex;align-items:center;justify-content:center;background:var(--white)}
.feature .circle span{width:115px;height:115px;border-radius:50%;background:var(--navy);display:flex;align-items:center;justify-content:center}
.feature h3{margin-top:18px;font-size:22px;line-height:31px;font-weight:500;color:var(--ink)}

.plant{height:1498px}
.center-head{left:0;width:1200px;text-align:center}
.plant .eyebrow{color:var(--ink)}
.plant .eyebrow .rule b{width:64px}
.plant h2{top:158px;font-size:58px;font-weight:500;color:var(--navy)}
.plant .lead{top:240px;font-size:15px;line-height:30px;color:#444}
.hire-img{position:absolute;width:458px;height:266px;border-radius:14px}
.hire-title{position:absolute;font-size:30px;font-weight:600;color:var(--ink)}
.hire-title::after{content:"";display:block;width:66px;height:4px;background:var(--navy);margin-top:10px}
.hire-copy{position:absolute;width:490px;font-size:14.5px;line-height:30px;color:#555}
.justify{text-align:justify}
.plant .btn{width:135px;height:35px}
.plant .btn-grey{left:511px;top:1357px;width:178px;height:61px}

.contact-band{height:443px;background:linear-gradient(90deg,#b6a23e 0%,#c9b04a 22%,#9a9360 38%,#3e5fa9 56%,#2e4fa0 100%)}
.contact-band .eyebrow{left:664px;top:100px;color:var(--white)}
.contact-band h2{left:664px;top:138px;font-size:50px;line-height:63px;font-weight:500;color:var(--white)}
.contact-band .btn{left:666px;top:292px;width:188px;height:55px}

.projects{height:1261px}
.projects .eyebrow{left:418px;top:126px;color:var(--ink)}
.projects .eyebrow .rule b{width:168px}
.projects h2{top:166px;font-size:60px;font-weight:500;color:var(--navy)}
.projects .lead{top:246px;font-size:15px;color:#444}
.card{position:absolute;top:323px;width:313px;height:566px;background:var(--white);border-radius:18px;box-shadow:0 3px 16px rgba(0,0,0,.16)}
.card h3{position:absolute;left:30px;width:270px;font-size:22px;line-height:27px;font-weight:500;color:var(--navy)}
.card .client{position:absolute;left:30px;font-size:18px;font-weight:600;color:var(--ink);white-space:nowrap}
.card .year{position:absolute;left:30px;font-size:15.5px;color:#444}
.card .btn{left:30px;width:108px;height:29px;font-size:10px}
.card .btn .arr{width:14px;height:14px}
.card .pic{position:absolute;left:10px;width:293px;border-radius:12px}
.card .notch{position:absolute;width:0;height:0;border-left:16px solid transparent;border-right:16px solid transparent}
.projects .btn-grey{left:511px;top:962px;width:178px;height:61px}
.partners{left:0;top:1134px;width:1200px;height:60px}
.partners .nav-arrow{position:absolute;top:16px;width:28px;height:28px;border-radius:50%;background:var(--navy-dark);display:flex;align-items:center;justify-content:center}
.partners .name{position:absolute;top:18px;font-size:17px;font-weight:600;color:var(--navy);white-space:nowrap;transform:translateX(-50%)}

.site-footer{height:437px;background:linear-gradient(180deg,#1f2866 0%,#1b2359 100%)}
.foot-brand{left:0;top:50px;width:1200px;text-align:center;color:var(--white)}
.foot-brand .mark{font-size:62px;font-weight:700;letter-spacing:3px;line-height:70px}
.foot-brand .sub{font-size:15px;font-weight:600;letter-spacing:6px}
.foot-contact{position:absolute;top:220px;display:flex;align-items:center;gap:14px;color:var(--white);font-size:12.5px;line-height:16px}
.foot-contact .ic{width:26px;height:26px;border-radius:4px;background:var(--white);display:flex;align-items:center;justify-content:center}
.foot-contact b{font-weight:600}
.foot-rule{left:76px;top:282px;width:1048px;height:1px;background:rgba(255,255,255,.35)}
.foot-nav{left:0;top:312px;width:1200px;display:flex;justify-content:center;gap:34px;font-size:13.5px;color:var(--white)}
.copyright{left:76px;top:392px;font-size:11.5px;color:var(--white)}
.social{left:989px;top:382px;display:flex;gap:7px}
.social i{display:block;width:29px;height:29px;border:1.5px solid var(--white);border-radius:3px}
</style>
</head>
<body>

<header class="site-header">
  <div class="abs brand"><div class="mark">HBR</div><div class="sub">PLANT HIRE</div></div>
  <div class="abs phone-pill"><span class="ic"><svg width="14" height="14" viewBox="0 0 24 24"><path d="M6.6 10.8a15 15 0 006.6 6.6l2.2-2.2a1 1 0 011-.25 11.4 11.4 0 003.6.6 1 1 0 011 1V20a1 1 0 01-1 1A17 17 0 013 4a1 1 0 011-1h3.5a1 1 0 011 1c0 1.25.2 2.45.6 3.6a1 1 0 01-.25 1z" fill="#222b6e"/></svg></span>1300 442 917</div>
  <div class="abs contact-btn">CONTACT US</div>
  <nav class="abs main-nav">
    <span class="active" style="left:0">HOME</span>
    <span style="left:77px">ABOUT US</span>
    <span style="left:186px">PLANT HIRE ▾</span>
    <span style="left:300px">MAJOR PROJECT SNAPSHOT</span>
    <span style="left:539px">POLICIES</span>
    <span style="left:633px">JOBS</span>
  </nav>
</header>

<section class="hero" role="img" aria-label="Yellow HBR excavator loading rock on a construction site under a blue sky">
  <h1 class="abs">HBR Heavy<br>Equipment Hire</h1>
  <p class="abs">Committed to superior quality<br>plant hire services.</p>
  <a class="btn btn-white">Learn More <span class="arr"><svg width="10" height="10" viewBox="0 0 10 10"><path d="M2 5h6M5 2l3 3-3 3" stroke="#fff" stroke-width="1.6" fill="none"/></svg></span></a>
  <div class="abs dots"><i class="on"></i><i></i><i></i><i></i></div>
</section>

<section class="about">
  <div class="eyebrow"><span>Who We Are</span><span class="rule"><i></i><b></b></span></div>
  <h2 class="abs">About HBR</h2>
  <p class="abs copy">Harlow Brentmere Resources Pty Ltd trading as HBR Heavy Equipment is a privately owned company that was established in 2010. Our founder saw a need in the market for a plant and equipment supplier who was committed to the successful delivery of client’s projects. With this vision and focus HBR has successfully seen our clients deliver on-time and on- budget.</p>
  <a class="btn btn-navy">Read More <span class="arr"><svg width="10" height="10" viewBox="0 0 10 10"><path d="M2 5h6M5 2l3 3-3 3" stroke="#222b6e" stroke-width="1.6" fill="none"/></svg></span></a>
  <div class="abs photo-frame"><div class="ph" role="img" aria-label="Company founder in a blue work shirt standing beside a white company vehicle"></div></div>
</section>

<section class="features">
  <div class="feature" style="left:178px"><div class="circle"><span><svg width="54" height="54" viewBox="0 0 54 54" fill="#fff"><path d="M10 30a17 17 0 0134 0z"/><rect x="7" y="30" width="40" height="5" rx="2"/><rect x="24" y="11" width="6" height="12" rx="2" fill="#222b6e"/><path d="M14 40c3 6 8 9 13 9s10-3 13-9z"/></svg></span></div><h3>20+ Years of<br>Experience</h3></div>
  <div class="feature" style="left:384px"><div class="circle"><span><svg width="56" height="56" viewBox="0 0 56 56" fill="#fff"><rect x="6" y="28" width="20" height="12" rx="2"/><rect x="8" y="20" width="12" height="9"/><path d="M26 30l10-16 12 8-3 3-9-5-7 12z"/><path d="M44 24l4 10h-8z"/><rect x="4" y="42" width="26" height="7" rx="3.5"/></svg></span></div><h3>100+ Machines<br>In Fleet</h3></div>
  <div class="feature" style="left:595px"><div class="circle"><span><svg width="56" height="56" viewBox="0 0 56 56" fill="#fff"><rect x="14" y="10" width="4" height="28"/><path d="M16 10l24 14-2 2-22-12z"/><rect x="8" y="36" width="22" height="10" rx="2"/><rect x="32" y="36" width="16" height="10" rx="2"/><path d="M38 26v8" stroke="#fff" stroke-width="2"/></svg></span></div><h3>QLD’s Largest<br>Suppliers</h3></div>
  <div class="feature" style="left:811px"><div class="circle"><span><svg width="54" height="54" viewBox="0 0 54 54" fill="#fff"><path d="M13 22a14 14 0 0128 0z"/><rect x="11" y="22" width="32" height="4" rx="2"/><path d="M10 48c1-9 8-14 17-14s16 5 17 14z"/><path d="M22 34l5 8 5-8" fill="#222b6e"/></svg></span></div><h3>Onsite<br>Servicing</h3></div>
  <div class="feature" style="left:1022px"><div class="circle"><span><svg width="54" height="54" viewBox="0 0 54 54" fill="#fff"><path d="M20 6h14l-3 10h-8z"/><rect x="18" y="18" width="18" height="4" rx="2"/><rect x="18" y="25" width="18" height="4" rx="2"/><rect x="18" y="32" width="18" height="4" rx="2"/><path d="M22 38h10l-2 10h-6z"/></svg></span></div><h3>Custom Machine<br>Attachments</h3></div>
</section>

<section class="plant">
  <div class="eyebrow" style="left:454px;top:116px"><span class="rule"><b></b><i></i></span><span>Who We Do</span><span class="rule"><i></i><b></b></span></div>
  <h2 class="abs center-head">Plant Hire</h2>
  <p class="abs center-head lead">Reliable Plant Hire Spanning Queensland &amp; Surrounds We Have One of the Largest<br>&amp; Most Versatile Fleets in South East Queensland.</p>

  <div class="hire-img" style="left:100px;top:339px;background:linear-gradient(160deg,#b9cfe6 0%,#d8dde2 38%,#e2773a 55%,#a98b62 80%,#8d7b5f 100%)" role="img" aria-label="Orange excavator digging on a school construction site"></div>
  <h3 class="hire-title" style="left:609px;top:351px">Excavators &amp; Diggers for Hire</h3>
  <p class="hire-copy justify" style="left:609px;top:414px">We are proud of our broad range of excavators fitted with state-of-the-art GPS, spanning reliable and trusted brands such as Ardmore excavators for hire, Torvane excavators for hire,</p>
  <a class="btn btn-navy" style="left:609px;top:554px">Read More <span class="arr"><svg width="10" height="10" viewBox="0 0 10 10"><path d="M2 5h6M5 2l3 3-3 3" stroke="#222b6e" stroke-width="1.6" fill="none"/></svg></span></a>

  <h3 class="hire-title" style="left:112px;top:684px">Dozers for Hire</h3>
  <p class="hire-copy justify" style="left:112px;top:745px">The most prolific brands of dozer manufacturers are Ardmore &amp; Torvane – and we have both machine brands available for hire based on your preference – in a range of sizes suitable for bulk earthworks and detailed earthworks.</p>
  <a class="btn btn-navy" style="left:112px;top:885px">Read More <span class="arr"><svg width="10" height="10" viewBox="0 0 10 10"><path d="M2 5h6M5 2l3 3-3 3" stroke="#222b6e" stroke-width="1.6" fill="none"/></svg></span></a>
  <div class="hire-img" style="left:640px;top:672px;background:linear-gradient(180deg,#8fb4de 0%,#b7c9da 30%,#d2b24a 55%,#8c7a55 85%,#7a6b50 100%)" role="img" aria-label="Yellow bulldozer parked on a gravel yard"></div>

  <div class="hire-img" style="left:100px;top:1024px;background:linear-gradient(180deg,#5d9be0 0%,#a9c7e8 35%,#e3b52f 55%,#c7a13a 75%,#d9cdb5 100%)" role="img" aria-label="Yellow articulated dump truck on a sunny site"></div>
  <h3 class="hire-title" style="left:609px;top:1048px">Dump Trucks For Hire</h3>
  <p class="hire-copy" style="left:609px;top:1111px">Our new and well-maintained fleet of articulated dump trucks for hire ranging from 25 tonne capacity through to 40 tonne. We own and operate a fleet of Ridgeline and Ardmore articulated dump trucks</p>
  <a class="btn btn-navy" style="left:609px;top:1236px">Read More <span class="arr"><svg width="10" height="10" viewBox="0 0 10 10"><path d="M2 5h6M5 2l3 3-3 3" stroke="#222b6e" stroke-width="1.6" fill="none"/></svg></span></a>

  <a class="btn btn-grey">View All <span class="arr"><svg width="12" height="12" viewBox="0 0 10 10"><path d="M2 5h6M5 2l3 3-3 3" stroke="#7d7d7d" stroke-width="1.6" fill="none"/></svg></span></a>
</section>

<section class="contact-band" role="img" aria-label="Yellow water truck on a site, fading into a blue brand panel">
  <div class="eyebrow"><span>Get In Touch</span><span class="rule"><i></i><b style="width:120px"></b></span></div>
  <h2 class="abs">Contact Us Today<br>For A FREE QUOTE</h2>
  <a class="btn btn-white">Get A Quote <span class="arr"><svg width="10" height="10" viewBox="0 0 10 10"><path d="M2 5h6M5 2l3 3-3 3" stroke="#fff" stroke-width="1.6" fill="none"/></svg></span></a>
</section>

<section class="projects">
  <div class="eyebrow"><span class="rule"><b></b><i></i></span><span>HBR Projects</span><span class="rule"><i></i><b></b></span></div>
  <h2 class="abs center-head">Major Project Snapshot</h2>
  <p class="abs center-head lead">We’re incredibly proud of our major project experience.</p>

  <div class="card" style="left:88px">
    <h3 style="top:55px">Riverbend Corridor<br>Project (RCP) Brisbane</h3>
    <p class="client" style="top:110px">Client – Ironbark Civil</p>
    <p class="year" style="top:150px">Commencement Year – 2017</p>
    <a class="btn btn-navy" style="top:206px">Read More <span class="arr"><svg width="8" height="8" viewBox="0 0 10 10"><path d="M2 5h6M5 2l3 3-3 3" stroke="#222b6e" stroke-width="1.8" fill="none"/></svg></span></a>
    <div class="pic" style="top:269px;height:293px;background:linear-gradient(180deg,#b5c9b0 0%,#7d9a6a 35%,#c59d3a 60%,#9a7a4f 100%)" role="img" aria-label="Yellow dozer working on a roadside earthworks site"></div>
    <div class="notch" style="left:140px;top:269px;border-top:16px solid #fff"></div>
  </div>

  <div class="card" style="left:443px">
    <div class="pic" style="top:8px;height:288px;background:linear-gradient(180deg,#9ec3e6 0%,#c7d6e3 35%,#5f7f98 55%,#c9663a 75%,#6a6f74 100%)" role="img" aria-label="Long-reach excavator on a barge working on a river"></div>
    <div class="notch" style="left:140px;top:280px;border-bottom:16px solid #fff"></div>
    <h3 style="top:332px">Wattlebank Drive<br>Upgrade, Brisbane</h3>
    <p class="client" style="top:398px">Client – Stonegate Group</p>
    <p class="year" style="top:438px">Commencement Year – 2016</p>
    <a class="btn btn-navy" style="top:488px">Read More <span class="arr"><svg width="8" height="8" viewBox="0 0 10 10"><path d="M2 5h6M5 2l3 3-3 3" stroke="#222b6e" stroke-width="1.8" fill="none"/></svg></span></a>
  </div>

  <div class="card" style="left:795px">
    <h3 style="top:55px">Eastway Upgrade<br>North Stage 2, Brisbane</h3>
    <p class="client" style="top:110px">Client – Stonegate Group</p>
    <p class="year" style="top:150px">Commencement Year – 2016</p>
    <a class="btn btn-navy" style="top:206px">Read More <span class="arr"><svg width="8" height="8" viewBox="0 0 10 10"><path d="M2 5h6M5 2l3 3-3 3" stroke="#222b6e" stroke-width="1.8" fill="none"/></svg></span></a>
    <div class="pic" style="top:269px;height:293px;background:linear-gradient(180deg,#6f8a5a 0%,#a8b19a 35%,#e07a3a 55%,#cfc7b9 80%,#b8b0a2 100%)" role="img" aria-label="Orange excavator on a cleared cutting beside bushland"></div>
    <div class="notch" style="left:140px;top:269px;border-top:16px solid #fff"></div>
  </div>

  <a class="btn btn-grey">View All <span class="arr"><svg width="12" height="12" viewBox="0 0 10 10"><path d="M2 5h6M5 2l3 3-3 3" stroke="#7d7d7d" stroke-width="1.6" fill="none"/></svg></span></a>

  <div class="abs partners">
    <span class="nav-arrow" style="left:66px"><svg width="10" height="10" viewBox="0 0 10 10"><path d="M7 1L3 5l4 4" stroke="#fff" stroke-width="1.8" fill="none"/></svg></span>
    <span class="name" style="left:188px">Quarrix</span>
    <span class="name" style="left:316px">Delvane</span>
    <span class="name" style="left:462px">Stonegate</span>
    <span class="name" style="left:600px">Corvel</span>
    <span class="name" style="left:736px">Norcrest</span>
    <span class="name" style="left:874px">Pellam</span>
    <span class="name" style="left:1012px">Brackwell</span>
    <span class="nav-arrow" style="left:1112px"><svg width="10" height="10" viewBox="0 0 10 10"><path d="M3 1l4 4-4 4" stroke="#fff" stroke-width="1.8" fill="none"/></svg></span>
  </div>
</section>

<footer class="site-footer">
  <div class="abs foot-brand"><div class="mark">HBR</div><div class="sub">PLANT HIRE</div></div>
  <div class="foot-contact" style="left:258px"><span class="ic"><svg width="14" height="14" viewBox="0 0 24 24"><path d="M6.6 10.8a15 15 0 006.6 6.6l2.2-2.2a1 1 0 011-.25 11.4 11.4 0 003.6.6 1 1 0 011 1V20a1 1 0 01-1 1A17 17 0 013 4a1 1 0 011-1h3.5a1 1 0 011 1c0 1.25.2 2.45.6 3.6a1 1 0 01-.25 1z" fill="#1f2866"/></svg></span><span><b>CALL US</b><br>1300 442 917</span></div>
  <div class="foot-contact" style="left:474px"><span class="ic"><svg width="14" height="12" viewBox="0 0 14 12"><rect x="0.5" y="0.5" width="13" height="11" fill="#1f2866"/><path d="M1 1l6 5 6-5" stroke="#fff" stroke-width="1.2" fill="none"/></svg></span><span><b>EMAIL US</b><br>info@hbrplanthire.com.au</span></div>
  <div class="foot-contact" style="left:762px"><span class="ic"><svg width="12" height="16" viewBox="0 0 12 16"><path d="M6 0a6 6 0 016 6c0 4.5-6 10-6 10S0 10.5 0 6a6 6 0 016-6z" fill="#1f2866"/><circle cx="6" cy="6" r="2.2" fill="#fff"/></svg></span><span>18 Tallowood Rd,<br>Coomera QLD 4209</span></div>
  <div class="abs foot-rule"></div>
  <nav class="abs foot-nav"><span>HOME</span><span>ABOUT US</span><span>PLANT HIRE</span><span>MAJOR PROJECT SNAPSHOT</span><span>POLICIES</span><span>JOBS</span><span>CONTACT US</span></nav>
  <p class="abs copyright">Copyright © 2023 All Rights Reserved By HBR Plant Hire</p>
  <div class="abs social"><i></i><i></i><i></i><i></i></div>
</footer>

</body>
</html>
```